Corporate Business Card

Very professional, Modern, Not to busy, include phone address email, website
(253) 617-4930, 18761 52nd Avenue S, Kent, WA 98047, martin@plumlinegroup.com, varkoworks.com

Target Market(s)

Manufacturing

Industry/Entity Type

Aero, machining, manufacturing, Off road racing

Contact Information for Business Card

Phone, address email, website

```html
<!DOCTYPE html>
<html lang="en">
<head>
<meta charset="utf-8">
<title>Varko Works – Business Card</title>
<link rel="stylesheet" href="https://fonts.googleapis.com/css2?family=Arimo:wght@400;700&display=swap">
<style>
  :root {
    --navy: #17356e;
    --red: #d6222c;
    --paper: #f7f7f7;
    --ink: #1c1c1c;
    --backdrop: #2a2b2d;
  }
  * { margin: 0; padding: 0; box-sizing: border-box; }
  html, body { width: 1200px; height: 900px; overflow: hidden; }
  body {
    background: var(--backdrop);
    font-family: "Arimo", Arial, sans-serif;
    position: relative;
  }
  .card {
    position: absolute;
    left: 285px;
    width: 630px;
    height: 360px;
    border-radius: 22px;
    overflow: hidden;
  }
  .card--front { top: 50px; background: var(--navy); }
  .card--back { top: 470px; background: var(--paper); }

  .wordmark {
    display: flex;
    align-items: center;
    gap: 14px;
    font-weight: 700;
    letter-spacing: 2px;
    text-transform: uppercase;
    white-space: nowrap;
  }
  .wordmark__square { display: block; background: var(--red); flex: none; }

  .card--front .wordmark {
    position: absolute;
    left: 0; right: 0; top: 0; bottom: 0;
    justify-content: center;
    color: #fff;
    font-size: 56px;
  }
  .card--front .wordmark__square { width: 26px; height: 26px; }

  .card--back .logo-zone {
    position: absolute;
    left: 0;
    top: 90px;
    width: 300px;
    height: 120px;
    display: flex;
    align-items: center;
    justify-content: center;
  }
  .card--back .wordmark {
    color: var(--navy);
    font-size: 24px;
    letter-spacing: 1px;
    gap: 9px;
  }
  .card--back .wordmark__square { width: 14px; height: 14px; }

  .divider {
    position: absolute;
    left: 300px;
    top: 90px;
    width: 2px;
    height: 180px;
    background: var(--navy);
  }
  .contact {
    position: absolute;
    left: 330px;
    top: 92px;
    color: var(--ink);
  }
  .contact__name {
    font-size: 26px;
    font-weight: 700;
    letter-spacing: 1px;
    color: var(--navy);
    text-transform: uppercase;
  }
  .contact__name .surname { color: var(--red); }
  .contact__role { font-size: 15px; margin: 2px 0 12px; letter-spacing: .5px; }
  .contact__address { font-size: 15px; line-height: 1.3; margin-bottom: 12px; }
  .contact__list { list-style: none; font-size: 15px; line-height: 1.5; }
  .contact__list li { display: flex; align-items: center; gap: 8px; }
  .contact__list svg { width: 13px; height: 13px; fill: var(--red); flex: none; }
</style>
</head>
<body>

<section class="card card--front" aria-label="Card front">
  <div class="wordmark"><span class="wordmark__square"></span>Varko Works</div>
</section>

<section class="card card--back" aria-label="Card back">
  <div class="logo-zone">
    <div class="wordmark"><span class="wordmark__square"></span>Varko Works</div>
  </div>
  <div class="divider"></div>
  <div class="contact">
    <p class="contact__name">Owen <span class="surname">Hartley</span></p>
    <p class="contact__role">Owner</p>
    <p class="contact__address">18761 52nd Avenue S, Kent<br>WA 98047</p>
    <ul class="contact__list">
      <li>
        <svg viewBox="0 0 24 24" aria-hidden="true"><path d="M6.6 10.8a15.1 15.1 0 0 0 6.6 6.6l2.2-2.2a1 1 0 0 1 1-.25 11.4 11.4 0 0 0 3.6.57 1 1 0 0 1 1 1V20a1 1 0 0 1-1 1A17 17 0 0 1 3 4a1 1 0 0 1 1-1h3.5a1 1 0 0 1 1 1c0 1.250.2 2.45.57 3.6a1 1 0 0 1-.25 1z"/></svg>
        (253) 617-4930
      </li>
      <li>
        <svg viewBox="0 0 24 24" aria-hidden="true"><path d="M2 5h20v14H2z M2 5l10 8 10-8" /></svg>
        martin@plumlinegroup.com
      </li>
      <li>
        <svg viewBox="0 0 24 24" aria-hidden="true"><path d="M12 2a10 10 0 1 0 0 20 10 10 0 0 0 0-20zm6.9 6h-2.9a15 15 0 0 0-1.4-3.6A8 8 0 0 1 18.9 8zM12 4a13 13 0 0 1 1.9 4h-3.8A13 13 0 0 1 12 4zM4.3 14a8 8 0 0 1 0-4h3.4a16 16 0 0 0 0 4zm.8 2h2.9a15 15 0 0 0 1.4 3.6A8 8 0 0 1 5.1 16zM8 8H5.1a8 8 0 0 1 4.3-3.6A15 15 0 0 0 8 8zm4 12a13 13 0 0 1-1.9-4h3.8A13 13 0 0 1 12 20zm2.3-6H9.7a14 14 0 0 1 0-4h4.6a14 14 0 0 1 0 4zm.3 5.6a15 15 0 0 0 1.4-3.6h2.9a8 8 0 0 1-4.3 3.6zM16.3 14a16 16 0 0 0 0-4h3.4a8 8 0 0 1 0 4z"/></svg>
        www.varkoworks.com
      </li>
    </ul>
  </div>
</section>

</body>
</html>
```